TL - business card

Tallow Partners is an insurance brokerage firm, inovative, proactive, vigorous, which aims to become the leader of the insurance brokers in Anfrica. We should like to get some designs which should be avoided also in Gray / Metallic for the Administration and Orange / Blue for the Managers (ike in the picture sent). The Blue / Green logo is not the correct one, but the source of the file. Please adjust the color accordingly for the business cards. 1 / Orange / Blue 2 / Gray / Metallic We want something classic but which is transmitted strenght, inovation, modernity and most of all, rapidity. We want something start-up like, very punchy and catching eye remaining profesional at the same time. Name: Dorian Whitlock Function: Managing Director Address: N ° 17/18 Rua Veloso - R / C 2B Direita - Bairro Mutamba - Luanda Tel: (+244) 947 582 316 Email: dorian.whitlock@tallow-p.example Website: www.tallow-p. example We want classic in the front and creative, colorfull at the back. The cards will be printed in relief, with very high quality of paper.
Insurance Broker
Colors
Designer to choose colors to be used in the design.

```html
<!DOCTYPE html>
<html lang="en">
<head>
<meta charset="utf-8">
<title>Tallow Partners – Business Card</title>
<link href="https://fonts.googleapis.com/css2?family=Montserrat:wght@400;600;700&display=swap" rel="stylesheet">
<style>
  :root {
    --stage: #b9b9b9;
    --sky: #2aa9e0;
    --sky-deep: #1f9bd4;
    --brand-green: #1b9a4a;
    --paper: #ffffff;
    --ink: #555a5f;
    --name-blue: #27a6df;
  }
  * { margin: 0; padding: 0; box-sizing: border-box; }
  html, body {
    width: 1200px; height: 930px; overflow: hidden;
    background: var(--stage);
    font-family: "Montserrat", Arial, sans-serif;
  }
  .canvas { position: relative; width: 1200px; height: 930px; }
  .card {
    position: absolute; width: 660px; height: 380px;
    border-radius: 26px; overflow: hidden;
    box-shadow: 0 8px 22px rgba(0,0,0,.25);
  }
  .card-front { left: 70px; top: 60px; background: var(--sky); }
  .card-back { left: 470px; top: 490px; background: var(--paper); }

  .front-mark {
    position: absolute; inset: 0;
    display: flex; flex-direction: column; align-items: center; justify-content: center; gap: 20px;
  }
  .front-mark .dot { width: 90px; height: 90px; border-radius: 50%; border: 8px solid #fff; }
  .front-mark .brand { color: #fff; font-weight: 700; font-size: 40px; letter-spacing: 1px; text-transform: uppercase; }

  .back-mark {
    position: absolute; right: 40px; top: 36px;
    display: flex; flex-direction: column; align-items: center; gap: 12px;
  }
  .back-mark .dot { width: 62px; height: 62px; border-radius: 50%; border: 6px solid var(--brand-green); }
  .back-mark .brand { color: var(--brand-green); font-weight: 700; font-size: 26px; text-transform: uppercase; }

  .divider { position: absolute; left: 90px; right: 40px; top: 236px; height: 2px; background: var(--sky); }
  .accent { position: absolute; left: 0; top: 188px; width: 12px; height: 40px; background: var(--sky); }

  .person { position: absolute; left: 44px; top: 182px; }
  .person .name { color: var(--name-blue); font-weight: 600; font-size: 28px; line-height: 1.1; }
  .person .role { color: var(--ink); font-size: 15px; margin-top: 2px; }

  .address {
    position: absolute; right: 40px; top: 258px;
    text-align: right; color: var(--ink); font-size: 15px; line-height: 1.45;
  }
  .contact { position: absolute; left: 90px; bottom: 34px; color: var(--ink); font-size: 16px; line-height: 1.6; }
  .contact li { list-style: none; display: flex; align-items: center; gap: 10px; }
  .contact svg { width: 13px; height: 13px; flex: none; }
</style>
</head>
<body>
<div class="canvas">
  <section class="card card-front">
    <div class="front-mark">
      <span class="dot"></span>
      <span class="brand">Tallow Partners</span>
    </div>
  </section>

  <section class="card card-back">
    <div class="back-mark">
      <span class="dot"></span>
      <span class="brand">Tallow Partners</span>
    </div>
    <span class="accent"></span>
    <div class="person">
      <p class="name">Dorian Whitlock</p>
      <p class="role">Managing Director</p>
    </div>
    <div class="divider"></div>
    <p class="address">N° 17/18 Rua Veloso<br>R / C 2B Direita<br>Bairro Mutamba - Luanda</p>
    <ul class="contact">
      <li>
        <svg viewBox="0 0 24 24" aria-hidden="true"><path fill="#27a6df" d="M6.6 10.8a15 15 0 0 0 6.6 6.6l2.2-2.2a1 1 0 0 1 1-.25 11.4 11.4 0 0 0 3.6.57 1 1 0 0 1 1 1V20a1 1 0 0 1-1 1A17 17 0 0 1 3 4a1 1 0 0 1 1-1h3.5a1 1 0 0 1 1 1c0 1.25.2 2.45.57 3.57a1 1 0 0 1-.25 1z"/></svg>
        +244 947 582 316
      </li>
      <li>
        <svg viewBox="0 0 24 24" aria-hidden="true"><rect x="2" y="5" width="20" height="14" rx="1" fill="none" stroke="#27a6df" stroke-width="2.4"/><path d="M2 6l10 7 10-7" fill="none" stroke="#27a6df" stroke-width="2.4"/></svg>
        dorian.whitlock@tallow-p.example
      </li>
    </ul>
  </section>
</div>
</body>
</html>
```